Verpackungsdesign für Kaffeerösterei
Zielgruppe
wir Rösten Kaffee. Wir haben uns darauf Spezialisiert Hochwertigen Premium Caffe Crema herzustellen und bieten auch nur diesen in Unserem Shop www.brunovel-roest.de an. wir bieten 250gr. 500gr. Kaffee an. .
Es kann gerne verrückt oder anders sein, dennoch aber sehr edel.
die Zielgruppe ist weitgestreut, aber laut unserern Daten ist die Ideale Zielgruppe der 52 Jährige Mann, der Wert auf Hochwertige Genussmittel legt und auch bereit ist mehr Geld dafür zu bezahlen.
ich habe bereits ein beispiel design und die Druckvorlage bereitgestellt.
Aufgabenstellung
das Konzept unserer Internetseite sollte berücksichtigt werden, ansonsten ist dem Kreativen kopf keine Grenzen gesetzt.

```html
<!DOCTYPE html>
<html lang="de">
<head>
<meta charset="utf-8">
<title>Brunovel – Cafe Crema 500g</title>
<link rel="stylesheet" href="https://fonts.googleapis.com/css2?family=Oranienbaum&family=Crimson+Text:wght@400;600&display=swap">
<style>
  :root {
    --stage: #e9e9e9;
    --bag: #0b0908;
    --bag-edge: #1a1613;
    --copper: #a57a58;
    --copper-soft: #b48a66;
    --gold: #d4a93c;
    --bean-dark: #1c130e;
    --bean-mid: #3a2a20;
    --seal: #24201b;
  }
  * { margin: 0; padding: 0; box-sizing: border-box; }
  html, body { width: 849px; height: 1200px; overflow: hidden; }
  body { background: var(--stage); position: relative; }

  .pack-front {
    position: absolute;
    left: 120px; top: 30px;
    width: 610px; height: 1140px;
    background: linear-gradient(180deg, var(--bag-edge) 0%, var(--bag) 30%, var(--bag) 100%);
    overflow: hidden;
  }
  .pack-front__seal-lines {
    position: absolute; left: 0; top: 0; width: 100%; height: 90px;
  }
  .bean-area {
    position: absolute; left: 0; top: 470px; width: 100%; height: 670px;
    background:
      radial-gradient(ellipse 60% 45% at 50% 55%, var(--bean-mid) 0%, rgba(58,42,32,0.5) 45%, rgba(11,9,8,0) 75%),
      radial-gradient(ellipse 30% 25% at 15% 20%, rgba(58,42,32,0.7) 0%, rgba(11,9,8,0) 70%),
      radial-gradient(ellipse 30% 25% at 88% 25%, rgba(58,42,32,0.7) 0%, rgba(11,9,8,0) 70%),
      linear-gradient(180deg, rgba(11,9,8,0) 0%, var(--bean-dark) 40%, var(--bean-dark) 100%);
  }
  .brand {
    position: absolute; left: 0; top: 245px; width: 100%;
    text-align: center;
    font-family: "Crimson Text", serif;
    font-weight: 600;
    font-size: 46px;
    letter-spacing: 4px;
    color: var(--gold);
  }
  .product-title {
    position: absolute; left: 0; top: 392px; width: 100%;
    text-align: center;
    font-family: "Oranienbaum", serif;
    font-size: 100px;
    line-height: 1;
    letter-spacing: 8px;
    color: var(--copper);
  }
  .blend {
    position: absolute; left: 0; top: 492px; width: 100%;
    text-align: center;
    font-family: "Crimson Text", serif;
    font-size: 21px;
    line-height: 29px;
    color: var(--copper);
  }
  .flavour-note {
    position: absolute; left: 0; top: 578px; width: 100%;
    text-align: center;
    font-family: "Crimson Text", serif;
    font-size: 21px;
    color: var(--copper);
  }
  .quality-seal {
    position: absolute; left: 308px; top: 616px;
    width: 176px; height: 176px;
  }
  .net-weight {
    position: absolute; left: 0; top: 1022px; width: 100%;
    text-align: center;
    font-family: "Crimson Text", serif;
    font-size: 42px;
    color: var(--copper-soft);
  }
</style>
</head>
<body>
  <main class="pack-front">
    <svg class="pack-front__seal-lines" viewBox="0 0 610 90" aria-hidden="true">
      <g stroke="#2a2521" stroke-width="1.2">
        <line x1="0" y1="12" x2="610" y2="12"/>
        <line x1="0" y1="28" x2="610" y2="28"/>
        <line x1="0" y1="44" x2="610" y2="44"/>
        <line x1="0" y1="58" x2="610" y2="58"/>
        <line x1="0" y1="72" x2="610" y2="72"/>
      </g>
    </svg>

    <div class="bean-area" role="img" aria-label="Geröstete Kaffeebohnen, dunkel ausgeleuchtet"></div>

    <div class="brand">BRUNOVEL</div>

    <h1 class="product-title">CAFE CREMA</h1>

    <p class="blend">70% Robusta<br>30% Hochland Arabica</p>

    <p class="flavour-note">Säurearm</p>

    <svg class="quality-seal" viewBox="0 0 176 176" aria-hidden="true">
      <circle cx="88" cy="88" r="86" fill="var(--seal)"/>
      <circle cx="88" cy="88" r="74" fill="none" stroke="var(--gold)" stroke-width="5"/>
      <circle cx="88" cy="88" r="46" fill="none" stroke="var(--gold)" stroke-width="2"/>
    </svg>

    <p class="net-weight">Net wt. 500g</p>
  </main>
</body>
</html>
```